Small Business Broker Business Card Design

A business card design for a small business brokerage, which is a financial service, not unlike real estate brokerage, but for small businesses such as laundromats, pizza shops, restaurants, cleaners etc. The designs should all be simple, more conservative in nature, using the colors and font of the logo. Again, think real estate Brokerage as a business context
Contact Information for Business Card
Name: Glen R. Harlow. Title: Small Business Advisor. Email: g.harlow@bayfieldcapitalworks.example. Mobile: (555) 274-3918. Office: (555) 806-2147. www.bayfieldcapitalworks.example

```html
<!DOCTYPE html>
<html lang="en">
<head>
<meta charset="utf-8">
<title>Bayfield Capital Works — Business Card</title>
<link rel="stylesheet" href="https://fonts.googleapis.com/css2?family=Montserrat:wght@400;600;700;800&family=Arimo:ital,wght@0,400;1,400&display=swap">
<style>
  :root {
    --navy: #183a6e;
    --green: #7ab833;
    --green-deep: #6aa82a;
    --ink: #4a4a4a;
    --rule: #8a8a8a;
    --paper: #ffffff;
    --backdrop: #e9ebe6;
  }
  * { box-sizing: border-box; margin: 0; padding: 0; }
  html, body { width: 1200px; height: 963px; overflow: hidden; }
  body {
    background: var(--backdrop);
    font-family: "Arimo", Arial, sans-serif;
    position: relative;
  }
  .card {
    position: absolute;
    left: 215px;
    width: 770px;
    height: 440px;
    border-radius: 36px;
    box-shadow: 0 10px 28px rgba(0,0,0,.18);
    overflow: hidden;
  }
  .card--front { top: 30px; background: var(--paper); }
  .card--back {
    top: 493px;
    background: linear-gradient(135deg, var(--green) 0%, var(--green-deep) 100%);
  }

  /* front */
  .brand {
    position: absolute;
    right: 70px;
    top: 70px;
    text-align: left;
  }
  .brand__row { display: flex; align-items: center; gap: 12px; }
  .brand__dot { width: 16px; height: 16px; border-radius: 50%; background: var(--green); }
  .brand__name {
    font-family: "Montserrat", sans-serif;
    font-weight: 800;
    font-size: 24px;
    letter-spacing: 1.5px;
    color: var(--navy);
    text-transform: uppercase;
    white-space: nowrap;
  }
  .brand__tagline {
    margin-top: 6px;
    font-family: "Montserrat", sans-serif;
    font-weight: 600;
    font-size: 10.5px;
    letter-spacing: 1.6px;
    color: var(--green);
    text-transform: uppercase;
    padding-left: 28px;
    white-space: nowrap;
  }
  .person { position: absolute; left: 60px; top: 175px; }
  .person__name {
    font-family: "Montserrat", sans-serif;
    font-weight: 800;
    font-size: 34px;
    letter-spacing: 1px;
    color: var(--navy);
    text-transform: uppercase;
  }
  .person__title {
    font-family: "Arimo", sans-serif;
    font-size: 20px;
    color: var(--green);
    margin-top: 2px;
  }
  .rule {
    position: absolute;
    left: 60px; right: 60px; top: 262px;
    height: 1.5px;
    background: var(--rule);
  }
  .contacts {
    position: absolute;
    top: 285px;
    list-style: none;
    font-size: 19px;
    color: var(--ink);
    font-style: italic;
    white-space: nowrap;
  }
  .contacts--phones { left: 60px; }
  .contacts--online { left: 340px; }
  .contacts li { display: flex; align-items: center; gap: 12px; height: 36px; }
  .contacts svg { width: 18px; height: 18px; flex: none; }

  /* back */
  .back-brand { position: absolute; left: 60px; top: 60px; color: var(--paper); }
  .back-brand__name {
    font-family: "Montserrat", sans-serif;
    font-weight: 800;
    font-size: 30px;
    letter-spacing: 2px;
    text-transform: uppercase;
    white-space: nowrap;
  }
  .back-brand__tagline {
    margin-top: 6px;
    font-family: "Montserrat", sans-serif;
    font-weight: 600;
    font-size: 13px;
    letter-spacing: 2.4px;
    text-transform: uppercase;
    white-space: nowrap;
  }
</style>
</head>
<body>

<section class="card card--front" aria-label="Business card front">
  <div class="brand">
    <div class="brand__row">
      <span class="brand__dot"></span>
      <span class="brand__name">Bayfield Capital Works, Inc</span>
    </div>
    <div class="brand__tagline">Buy or sell a neighborhood business with trust</div>
  </div>

  <div class="person">
    <h1 class="person__name">Glen R. Harlow</h1>
    <p class="person__title">Small Business Advisor</p>
  </div>

  <div class="rule"></div>

  <ul class="contacts contacts--phones">
    <li>
      <svg viewBox="0 0 24 24" fill="none" stroke="var(--green)" stroke-width="2.4" stroke-linecap="round">
        <path d="M6 3l3 4-2 2c1 3 4 6 7 7l2-2 4 3-2 3C10 20 4 14 3 6z" fill="var(--green)" stroke="none"/>
        <path d="M14 6a4 4 0 0 1 4 4M14 2a8 8 0 0 1 8 8"/>
      </svg>
      (555) 806-2147
    </li>
    <li>
      <svg viewBox="0 0 24 24" fill="none" stroke="var(--green)" stroke-width="2.4">
        <rect x="6" y="2" width="12" height="20" rx="2"/>
        <line x1="10" y1="18" x2="14" y2="18"/>
      </svg>
      (555) 274-3918
    </li>
  </ul>

  <ul class="contacts contacts--online">
    <li>
      <svg viewBox="0 0 24 24" fill="none" stroke="var(--green)" stroke-width="2.2">
        <rect x="2" y="5" width="20" height="14" rx="1"/>
        <path d="M2 6l10 7 10-7"/>
      </svg>
      g.harlow@bayfieldcapitalworks.example
    </li>
    <li>
      <svg viewBox="0 0 24 24" fill="none" stroke="var(--green)" stroke-width="2">
        <circle cx="12" cy="12" r="10"/>
        <ellipse cx="12" cy="12" rx="4.5" ry="10"/>
        <line x1="2" y1="12" x2="22" y2="12"/>
        <path d="M4 7h16M4 17h16"/>
      </svg>
      www.bayfieldcapitalworks.example
    </li>
  </ul>
</section>

<section class="card card--back" aria-label="Business card back">
  <div class="back-brand">
    <div class="back-brand__name">Bayfield Capital Works, Inc</div>
    <div class="back-brand__tagline">Buy or sell a neighborhood business with trust</div>
  </div>
</section>

</body>
</html>
```